New Business Card Design Project

Use the flyer uploaded and website www.brightoakbuilders.com for inspiration.
List Our Services on Backside of business cards
Marcus Delling
Harborline Builders Inc.
Licensed General Contractors
858-471-6093

Contact Information for Business Card

Use the flyer uploaded and website www.brightoakbuilders.com for inspiration. List Our Services on Backside of business cards Marcus Delling Harborline Builders Inc. Licensed General Contractors 858-471-6093

```html
<!DOCTYPE html>
<html lang="en">
<head>
<meta charset="utf-8">
<title>Harborline Builders – Business Cards</title>
<link href="https://fonts.googleapis.com/css2?family=Cinzel:wght@500&family=Montserrat:wght@400;500&display=swap" rel="stylesheet">
<style>
  :root {
    --page-bg: #1c1c1e;
    --card-bg: #121214;
    --ink: #f4f4f4;
    --ink-soft: #d9d9d9;
  }
  * { margin: 0; padding: 0; box-sizing: border-box; }
  html, body { width: 1200px; height: 912px; overflow: hidden; }
  body {
    background: var(--page-bg);
    font-family: "Montserrat", sans-serif;
    color: var(--ink);
    position: relative;
  }
  .card {
    position: absolute;
    width: 620px;
    height: 354px;
    background: var(--card-bg);
    border-radius: 16px;
    box-shadow: 0 18px 40px rgba(0,0,0,0.55);
    overflow: hidden;
  }
  .card--front { left: 290px; top: 74px; }
  .card--back  { left: 290px; top: 484px; }

  .brand {
    display: flex;
    align-items: center;
    gap: 12px;
  }
  .brand__mark {
    width: 14px; height: 14px;
    background: var(--ink);
    flex: none;
  }
  .brand__name {
    font-family: "Montserrat", sans-serif;
    font-weight: 500;
    font-size: 26px;
    letter-spacing: 3px;
    text-transform: uppercase;
    color: var(--ink);
    white-space: nowrap;
  }

  /* Front */
  .card--front .brand {
    position: absolute;
    top: 110px; left: 0; right: 0;
    justify-content: center;
  }
  .services {
    position: absolute;
    top: 210px; left: 0; right: 0;
    text-align: center;
    font-size: 17px;
    line-height: 30px;
    color: var(--ink-soft);
  }

  /* Back */
  .card--back .brand {
    position: absolute;
    top: 126px; left: 60px;
  }
  .card--back .brand__mark { width: 12px; height: 12px; }
  .card--back .brand__name { font-size: 20px; letter-spacing: 2.5px; }
  .contact {
    position: absolute;
    left: 60px; top: 190px;
    list-style: none;
    font-size: 15px;
    line-height: 27px;
    color: var(--ink-soft);
  }
  .contact li { display: flex; align-items: center; gap: 10px; }
  .contact svg { width: 13px; height: 13px; flex: none; }
  .contact__company { margin-top: 14px; font-size: 16px; color: var(--ink); }

  .person {
    position: absolute;
    right: 36px; top: 52px;
    text-align: right;
  }
  .person__name {
    font-family: "Cinzel", serif;
    font-weight: 500;
    font-size: 22px;
    letter-spacing: 1px;
    text-transform: uppercase;
    color: var(--ink);
    white-space: nowrap;
  }
  .person__title {
    font-size: 13px;
    color: var(--ink-soft);
    margin-top: 4px;
    white-space: nowrap;
  }
  .accent-bar {
    position: absolute;
    right: 0; top: 50px;
    width: 20px; height: 40px;
    background: var(--ink);
  }
</style>
</head>
<body>

  <section class="card card--front" aria-label="Business card front">
    <div class="brand">
      <span class="brand__mark"></span>
      <span class="brand__name">Harborline Builders</span>
    </div>
    <p class="services">
      Painting • Flooring • Kitchens • Custom Renovations<br>
      Bathrooms • Energy Efficienct Upgrades
    </p>
  </section>

  <section class="card card--back" aria-label="Business card back">
    <div class="accent-bar"></div>
    <div class="person">
      <p class="person__name">Marcus Delling</p>
      <p class="person__title">Licensed General Contractors</p>
    </div>

    <div class="brand">
      <span class="brand__mark"></span>
      <span class="brand__name">Harborline Builders</span>
    </div>

    <ul class="contact">
      <li>
        <svg viewBox="0 0 16 16" aria-hidden="true"><path fill="#f4f4f4" d="M3.5 1.5l2.5 0 1 3.5-1.6 1.1c.8 1.8 2.2 3.2 4 4l1.1-1.6 3.5 1v2.5c0 .8-.7 1.5-1.5 1.5C6.8 13.5 2 8.7 2 3c0-.8.7-1.5 1.5-1.5z"/></svg>
        858-471-6093
      </li>
      <li>
        <svg viewBox="0 0 16 16" aria-hidden="true"><rect x="1" y="3" width="14" height="10" fill="#f4f4f4"/><path d="M1 3l7 6 7-6" fill="none" stroke="#121214" stroke-width="1.4"/></svg>
        info@brightoakbuilders.com
      </li>
      <li>
        <svg viewBox="0 0 16 16" aria-hidden="true"><circle cx="8" cy="8" r="6.5" fill="none" stroke="#f4f4f4" stroke-width="1.4"/><ellipse cx="8" cy="8" rx="2.8" ry="6.5" fill="none" stroke="#f4f4f4" stroke-width="1.2"/><path d="M1.5 8h13" stroke="#f4f4f4" stroke-width="1.2"/></svg>
        www.brightoakbuilders.com
      </li>
      <li class="contact__company">Harborline Builders Inc.</li>
    </ul>
  </section>

</body>
</html>
```